VOMRA Pty Ltd Business Card

Looking for a simple yet eye-catching double-sided business card design using my company logo on one side and contact details on the other.

Target Market(s)

Government

Industry/Entity Type

Communication Systems Engineering

Contact Information for Business Card

VOMRA Pty Ltd

Requirements
Nice to have
• Would be great to have a QR code so details can be scanned into contacts

```html
<!DOCTYPE html>
<html lang="en">
<head>
<meta charset="utf-8">
<title>VOMRA Pty Ltd Business Card</title>
<link href="https://fonts.googleapis.com/css2?family=Open+Sans:wght@400;700&display=swap" rel="stylesheet">
<style>
  :root {
    --page: #e6e7e8;
    --slate: #37414a;
    --charcoal: #1e1f20;
    --white: #ffffff;
    --muted: #dfe3e6;
  }
  * { margin: 0; padding: 0; box-sizing: border-box; }
  html, body { width: 1200px; height: 780px; overflow: hidden; }
  body {
    background: var(--page);
    font-family: "Open Sans", sans-serif;
    display: flex;
    align-items: center;
    justify-content: center;
    gap: 40px;
  }
  .card {
    width: 540px;
    height: 309px;
    position: relative;
    overflow: hidden;
    box-shadow: 0 6px 18px rgba(0,0,0,0.18);
  }

  /* Front side */
  .card-front {
    background: var(--slate);
    display: flex;
    align-items: center;
    justify-content: center;
  }
  .brand {
    display: flex;
    align-items: center;
    gap: 16px;
    color: var(--white);
    font-weight: 700;
  }
  .brand-mark {
    background: var(--white);
    border-radius: 50%;
  }
  .card-front .brand { font-size: 64px; letter-spacing: 4px; }
  .card-front .brand-mark { width: 46px; height: 46px; }

  /* Back side */
  .card-back { background: var(--slate); }
  .back-band {
    position: absolute;
    left: 0; top: 0;
    width: 100%;
    height: 182px;
    background: var(--charcoal);
  }
  .card-back .brand {
    position: absolute;
    left: 34px;
    top: 52px;
    font-size: 44px;
    letter-spacing: 3px;
    gap: 12px;
  }
  .card-back .brand-mark { width: 30px; height: 30px; }
  .holder {
    position: absolute;
    right: 46px;
    top: 104px;
    text-align: right;
    color: var(--white);
  }
  .holder-name { font-size: 26px; font-weight: 700; line-height: 1.1; }
  .holder-role { font-size: 15px; font-weight: 400; }
  .edge-tab {
    position: absolute;
    right: 0;
    top: 104px;
    width: 28px;
    height: 56px;
    background: var(--white);
  }
  .contact {
    position: absolute;
    left: 34px;
    top: 194px;
    color: var(--muted);
    font-size: 12.5px;
    line-height: 1.45;
    list-style: none;
  }
  .contact li { display: flex; align-items: center; gap: 7px; }
  .contact .address { padding-left: 19px; margin-bottom: 2px; }
  .contact svg { width: 12px; height: 12px; flex: none; fill: var(--muted); }
</style>
</head>
<body>

  <section class="card card-front" aria-label="Card front">
    <div class="brand">
      <span class="brand-mark"></span>
      <span class="brand-name">VOMRA</span>
    </div>
  </section>

  <section class="card card-back" aria-label="Card back">
    <div class="back-band"></div>
    <div class="brand">
      <span class="brand-mark"></span>
      <span class="brand-name">VOMRA</span>
    </div>
    <div class="holder">
      <p class="holder-name">Jordan Hale</p>
      <p class="holder-role">Co-Founder</p>
    </div>
    <div class="edge-tab"></div>
    <ul class="contact">
      <li class="address">14-16 Ridgeway Lane Northbrook<br>NSW 2150 Australia</li>
      <li>
        <svg viewBox="0 0 24 24" aria-hidden="true"><path d="M6.6 10.8a15.1 15.1 0 0 0 6.6 6.6l2.2-2.2a1 1 0 0 1 1-.25 11.4 11.4 0 0 0 3.6.57 1 1 0 0 1 1 1V20a1 1 0 0 1-1 1A17 17 0 0 1 3 4a1 1 0 0 1 1-1h3.5a1 1 0 0 1 1 1c0 1.25.2 2.45.57 3.57a1 1 0 0 1-.25 1z"/></svg>
        (555) 014-2291
      </li>
      <li>
        <svg viewBox="0 0 24 24" aria-hidden="true"><path d="M12 2a10 10 0 1 0 0 20 10 10 0 0 0 0-20zm6.9 6h-2.9a15.6 15.6 0 0 0-1.4-3.6A8 8 0 0 1 18.9 8zM12 4a14 14 0 0 1 1.9 4h-3.8A14 14 0 0 1 12 4zM4.3 14a8 8 0 0 1 0-4h3.3a16 16 0 0 0 0 4zm.8 2h2.9a15.6 15.6 0 0 0 1.4 3.6A8 8 0 0 1 5.1 16zM8 8H5.1a8 8 0 0 1 4.3-3.6A15.6 15.6 0 0 0 8 8zm4 12a14 14 0 0 1-1.9-4h3.8A14 14 0 0 1 12 20zm2.3-6H9.7a14.6 14.6 0 0 1 0-4h4.6a14.6 14.6 0 0 1 0 4zm.3 5.6a15.6 15.6 0 0 0 1.4-3.6h2.9a8 8 0 0 1-4.3 3.6zm1.8-5.6a16 16 0 0 0 0-4h3.3a8 8 0 0 1 0 4z"/></svg>
        www.vomra.com.au
      </li>
      <li>
        <svg viewBox="0 0 24 24" aria-hidden="true"><path d="M3 5h18a1 1 0 0 1 1 1v12a1 1 0 0 1-1 1H3a1 1 0 0 1-1-1V6a1 1 0 0 1 1-1zm1 2.3V17h16V7.3l-8 5.4z M5.2 7 12 11.5 18.8 7z"/></svg>
        admin@vomra.com.au
      </li>
    </ul>
  </section>

</body>
</html>
```